I need a logo that demonstrates multiple of the same with one of a distinguishing feature. I would like something that can be recognisable in silhouette format. The business designs Management systems bespoke the to the company helping them pre-qualify for work.
Something that can demonstrate a distinction between a collective group non of which are the same in shape or size, with the largest of these not the distinguished object (or something to that effect).
This is a new business no logo or artwork exists.
Target Market(s)
Small to Medium Size enterprises in the city and rural areas. Looking to make the step up.
Industry/Entity Type
Manufacture
Contact Information for Business Card
room for, Name, Email, phone number
Font styles to use
Requirements
Must have
- would like the silhouette to be recognisable
Nice to have
- would like it to incorporate the name Keystone Advisory Frameworks.
- Would like the same logo to be on both business cards and on corporate shirts
Should not have
- anything that may exclude rural trade or manufacturing.
- I don't want to appear as corporate, just professional

```html
<!DOCTYPE html>
<html lang="en">
<head>
<meta charset="utf-8">
<title>Keystone Advisory Frameworks – Business Card</title>
<link href="https://fonts.googleapis.com/css2?family=Open+Sans:wght@400;700&display=swap" rel="stylesheet">
<style>
  :root {
    --orange: #f07124;
    --ink: #1e1e1e;
    --paper: #ffffff;
    --backdrop: #ecebe8;
    --edge: #d9d6d0;
  }
  * { box-sizing: border-box; margin: 0; padding: 0; }
  html, body {
    width: 1200px;
    height: 900px;
    overflow: hidden;
    background: var(--backdrop);
    font-family: "Open Sans", Arial, sans-serif;
  }
  .stage { position: relative; width: 1200px; height: 900px; }

  .card {
    position: absolute;
    width: 600px;
    height: 343px;
    border: 1px solid var(--edge);
  }

  /* Front side */
  .card-front {
    left: 150px;
    top: 150px;
    background: var(--orange);
  }
  .card-front .brand-name {
    position: absolute;
    right: 40px;
    bottom: 110px;
    color: var(--paper);
    font-size: 28px;
    font-weight: 400;
    letter-spacing: 0.5px;
  }

  /* Back side */
  .card-back {
    left: 450px;
    top: 390px;
    background: var(--paper);
  }
  .contact {
    position: absolute;
    left: 335px;
    top: 34px;
    color: var(--ink);
    font-size: 13px;
    line-height: 1.45;
  }
  .contact .person-name {
    color: var(--orange);
    font-size: 17px;
    font-weight: 700;
    line-height: 1.2;
  }
  .contact .role { margin-bottom: 14px; }
  .contact .address { margin-bottom: 12px; }
  .contact-list { list-style: none; }
  .contact-list li {
    display: flex;
    align-items: center;
    gap: 10px;
  }
  .contact-list svg { width: 11px; height: 11px; flex: none; }

  .brand-lockup {
    position: absolute;
    left: 40px;
    bottom: 48px;
    display: flex;
    align-items: center;
    gap: 14px;
  }
  .brand-lockup .brand-square {
    width: 30px;
    height: 30px;
    background: var(--orange);
  }
  .brand-lockup .brand-name {
    color: var(--orange);
    font-size: 26px;
    font-weight: 400;
    letter-spacing: 0.5px;
  }
</style>
</head>
<body>
<main class="stage">

  <section class="card card-front" aria-label="Business card front">
    <p class="brand-name">Keystone Advisory Frameworks</p>
  </section>

  <section class="card card-back" aria-label="Business card back">
    <div class="contact">
      <p class="person-name">Daniel Hartley</p>
      <p class="role">Managing Director</p>
      <p class="address">48, Mill Lane Works<br>Northshire, 204817.</p>
      <ul class="contact-list">
        <li>
          <svg viewBox="0 0 24 24" aria-hidden="true"><path fill="var(--orange)" d="M6.6 10.8a15.1 15.1 0 0 0 6.6 6.6l2.2-2.2a1 1 0 0 1 1-.25 11.4 11.4 0 0 0 3.6.57 1 1 0 0 1 1 1V20a1 1 0 0 1-1 1A17 17 0 0 1 3 4a1 1 0 0 1 1-1h3.5a1 1 0 0 1 1 1c0 1.25.2 2.45.57 3.57a1 1 0 0 1-.25 1z"/></svg>
          <span>044-987 654 321</span>
        </li>
        <li>
          <svg viewBox="0 0 24 24" aria-hidden="true"><path fill="var(--orange)" d="M2 5h20v14H2z"/><path fill="none" stroke="var(--paper)" stroke-width="2" d="M3 6l9 7 9-7"/></svg>
          <span>info@keystonefw.com</span>
        </li>
        <li>
          <svg viewBox="0 0 24 24" aria-hidden="true"><path fill="none" stroke="var(--orange)" stroke-width="3" stroke-linecap="round" d="M10 14a4 4 0 0 0 5.6 0l3.2-3.2a4 4 0 0 0-5.6-5.6L12 6.4M14 10a4 4 0 0 0-5.6 0l-3.2 3.2a4 4 0 0 0 5.6 5.6L12 17.6"/></svg>
          <span>www.keystonefw.com</span>
        </li>
      </ul>
    </div>

    <div class="brand-lockup">
      <span class="brand-square" aria-hidden="true"></span>
      <p class="brand-name">Keystone Advisory Frameworks</p>
    </div>
  </section>

</main>
</body>
</html>
```